Need a small Brochure Designing for a High Tech LED Spotlight

This is an expensive product and the best of it's kind in the world, so it needs to be marketed to intelligent, forward thinking people who appreciate and pay for excellent design and innovation. The type of people who buy Quince products i guess. It needs to be clean. The colours do not need to be in keep with our website, but our logo does need to be on the brochure. I have attached a dcoument with all the text, the order the text goes in and an idea of how i want the first page to look. All images and logos have been attached too.

Target Market(s)

This is aimed at people with high disposible incomes who spend money on the best designed products and the latest technology. The type of people who buy Quince products.

Industry/Entity Type

Product

Requirements
Must have
• The work needs to be editable by us using indesign

The pages need to be A5. I'm not sure how many pages the brochure needs to be as it does need to be clean and be spaced out well. On the file that contains the text i've indicated that 8 pages would be good.

The logos i attached - 1) Brava Product Design Award, 2) K Technology Award, 3) Tall Oak Design Award and 4) Keen Form Award all need to be at the bottom of the front page, quite small, but still able to see them well.

- Needs to have a QR code so that smart phones can scan the code and be taken to a zen pier clip - QR code is attached.
- Needs to have Tumbolt Icon - @BrightNookCo
Nice to have
• Nice to remind customers on each page that the product has a 5 year Warranty and we have a 365 day Returns Policy.

```html
<!DOCTYPE html>
<html lang="en">
<head>
<meta charset="utf-8">
<title>H7 LED Spotlight – Brochure Spread</title>
<link rel="stylesheet" href="https://fonts.googleapis.com/css2?family=Quicksand:wght@300;400&display=swap">
<style>
  :root {
    --page: #f2f2f1;
    --page-shade: #dcdcda;
    --accent: #d3162e;
    --text: #5a5a5a;
    --photo-a: #c9ced0;
    --photo-b: #5f7f7c;
  }
  * { margin: 0; padding: 0; box-sizing: border-box; }
  html, body { width: 1200px; height: 848px; overflow: hidden; background: #e6e6e6; }
  body { font-family: "Quicksand", sans-serif; color: var(--text); }
  .spread { position: relative; width: 1200px; height: 848px; display: flex; }
  .page { position: relative; width: 600px; height: 848px; background: var(--page); }
  .page--left { background: linear-gradient(to right, var(--page) 92%, var(--page-shade)); }
  .page--right { background: linear-gradient(to left, var(--page) 92%, var(--page-shade)); }
  .section { position: absolute; }
  .page--left .section { left: 18px; width: 566px; }
  .page--right .section { left: 22px; width: 566px; }
  .section__title {
    font-weight: 400; font-size: 24px; color: var(--accent);
    margin-bottom: 18px; letter-spacing: 0.2px;
  }
  .section p {
    font-weight: 300; font-size: 12.8px; line-height: 1.5;
    text-align: center; margin-bottom: 16px; padding: 0 6px;
  }
  .photo {
    position: absolute; left: 165px; top: 632px; width: 284px; height: 190px;
    background: linear-gradient(120deg, var(--photo-a) 0%, var(--photo-a) 45%, var(--photo-b) 75%, #8a9e9c 100%);
  }
  .dimensions { display: grid; grid-template-columns: 120px 1fr; font-weight: 300; font-size: 12.8px; line-height: 1.5; margin-bottom: 16px; }
  .dimensions dt { position: relative; }
  .dimensions dt::after { content: "-"; position: absolute; left: 115px; }
  .dimensions dd { text-align: center; padding-left: 100px; }
</style>
</head>
<body>
<main class="spread">
  <article class="page page--left">
    <section class="section" style="top:22px">
      <h2 class="section__title">Heat Dissipation</h2>
      <p>The brightness of all LEDs deteriorates over time. Just how quickly, though, is almost exclusively down to how well the lamp can dissipate heat.</p>
      <p>Heat is the biggest enemy of the LED. Without proper heat dissipation, the critical components of any LED lamp will fail or degrade quickly. So if the LED spotlight doesn’t have a well-designed, thorough heat dissipation system, the quality of light will easily degrade to an unacceptable level, with the LED simply failing very quickly.</p>
      <p>The H7 7w is crafted from the finest raw materials and uses a cutting edge heat dissipation system similar to that used to cool fuel tanks on Orbitum space shuttles and brake callipers on Grand Circuit cars.</p>
      <p>This beautiful, intuitive patented design has won multiple international awards.</p>
    </section>
    <section class="section" style="top:380px">
      <h2 class="section__title">Brightness</h2>
      <p>Lumaro manufacture the most advanced and powerful LED chips in the world. While rival companies now produce very reasonable alternatives, there’s still no substitute for Lumaro.</p>
      <p>The H7 uses the very latest Lumaro LX-E Chip, which produces 580 warm white lumens. With 83 lumens per watt, the H7 is considerably more powerful than a 50w halogen – and any other LED spot.</p>
      <p>A Veltra IS-60 integrating sphere – a rare and very expensive piece of equipment – is used to measure the total light radiated in all directions from the lamp, giving customers a 100% accurate measurement of its so that the total power (or “flux”).</p>
    </section>
    <div class="photo" role="img" aria-label="Photograph of a large open integrating sphere in a testing laboratory"></div>
  </article>

  <article class="page page--right">
    <section class="section" style="top:26px">
      <h2 class="section__title">Life Span</h2>
      <p>As with the brightness testing on the H7, the method used to determine the lamp’s lifespan of this LED Spotlight is also a highly skilled and time consuming exercise known as accelerated testing.</p>
      <p>We use an algorithm that, after around 6,000 hours of testing, calculates the number of hours remaining before the LED Lamp will start to lose a significant amount of its brightness.</p>
      <p>Tests take up to 10 months to complete, ensuring that customers get a product with real staying power.</p>
    </section>
    <section class="section" style="top:344px">
      <h2 class="section__title">Easy Installation</h2>
      <p>The H7 comes in two standard fittings: GU10 (twist and lock) and MR16 (twin pin). Installation is simple: just take your old halogens out and put the H7 in.</p>
      <p>The product Dimensions are:</p>
      <dl class="dimensions">
        <dt>GU10</dt><dd>Length 60mm x Width 50mm</dd>
        <dt>MR16</dt><dd>Length 45.5mm x Width 50mm</dd>
      </dl>
      <p>Please note: the dimmable H7 only comes in GU10 fitting.</p>
    </section>
    <section class="section" style="top:642px">
      <h2 class="section__title">Maintenance</h2>
      <p>With an incredible lifespan of 40,000 hours, the H7 will last for an average of over 18 years if used for six hours a day, 365 days a year. With a lifespan like this, savings on replacing failed lamps are enormous.</p>
    </section>
  </article>
</main>
</body>
</html>
```